Computer Company needs a Business card design

We need a business card design for our business. We assist people to transition to the KVS (Kestrel Vantage Scheme). The Verandal Crown Office-owned kvs™ network is a brand new telecommunications network currently being rolled out across Australia, giving access to a reliable broadband connection. Our niche market will predominantly be domestic customers in the 50+ age bracket. The assistance that we provide is everything from arranging the equipment, arranging the plan and contract term, appointment times, final testing of the network and any tweaks that need to be made. We basically PM the transition from start to finish. The business card design should be minimalist, should communicate loyalty and stability, should be easy to read and clearly explain what we do. We have asked for front and back. However, the back of the card does not have to include much information at all. It could be just a small design, or a repeat of our phone number. Up to you. The attached file only says what is required on the card. It does not specify where to arrange the text, what fonts to use, etc etc. As much as we would like to give you more info, due to our very limited design ability, we are not really able to send you any rough, or otherwise, designs of what we are after. Hopefully the above description is enough for you.

```html
<!DOCTYPE html>
<html lang="en">
<head>
<meta charset="utf-8">
<title>kvs Done Simply – Business Card</title>
<link rel="stylesheet" href="https://fonts.googleapis.com/css2?family=Questrial&display=swap">
<style>
  :root {
    --page-bg: #b9b9b9;
    --brand-blue: #0a86ad;
    --brand-orange: #ef880f;
    --card-white: #f6f6f6;
    --text-grey: #555555;
    --divider-grey: #9a9a9a;
  }
  html, body {
    margin: 0;
    padding: 0;
    width: 1200px;
    height: 960px;
    overflow: hidden;
    background: var(--page-bg);
    font-family: "Questrial", "Century Gothic", sans-serif;
  }
  .canvas {
    position: relative;
    width: 1200px;
    height: 960px;
  }
  .card {
    position: absolute;
    left: 320px;
    width: 600px;
    box-shadow: 0 4px 10px rgba(0,0,0,0.25);
  }
  .card-front {
    top: 108px;
    height: 332px;
    background: var(--brand-blue);
    display: flex;
    align-items: center;
    justify-content: center;
  }
  .card-front .wordmark {
    color: #ffffff;
    font-size: 54px;
    letter-spacing: -0.5px;
    line-height: 1;
  }
  .card-back {
    top: 493px;
    height: 344px;
    background: var(--card-white);
  }
  .card-back .wordmark {
    position: absolute;
    left: 35px;
    top: 154px;
    color: var(--brand-blue);
    font-size: 30px;
    letter-spacing: -0.3px;
    line-height: 1;
  }
  .divider {
    position: absolute;
    left: 301px;
    top: 112px;
    width: 1px;
    height: 120px;
    background: var(--divider-grey);
  }
  .contact-block {
    position: absolute;
    left: 322px;
    top: 114px;
  }
  .person-name {
    margin: 0;
    color: var(--brand-blue);
    font-size: 21px;
    font-weight: 700;
    letter-spacing: 1px;
    line-height: 1.1;
  }
  .person-role {
    margin: 2px 0 14px;
    color: var(--brand-orange);
    font-size: 15px;
    letter-spacing: 0.5px;
  }
  .contact-list {
    list-style: none;
    margin: 0;
    padding: 0;
  }
  .contact-list li {
    display: flex;
    align-items: center;
    gap: 9px;
    color: var(--text-grey);
    font-size: 14.5px;
    line-height: 19.5px;
  }
  .contact-list svg {
    width: 12px;
    height: 12px;
    fill: var(--brand-blue);
  }
  .footer-band {
    position: absolute;
    left: 0;
    right: 0;
    bottom: 0;
    height: 10px;
    display: flex;
    gap: 2px;
    background: #ffffff;
  }
  .footer-band span { flex: 1; }
  .band-blue { background: var(--brand-blue); }
  .band-orange { background: var(--brand-orange); }
</style>
</head>
<body>
<div class="canvas">
  <section class="card card-front">
    <div class="wordmark">kvs Done Simply</div>
  </section>

  <section class="card card-back">
    <div class="wordmark">kvs Done Simply</div>
    <div class="divider"></div>
    <div class="contact-block">
      <h1 class="person-name">OWEN TARRANT</h1>
      <p class="person-role">CEO/FOUNDER</p>
      <ul class="contact-list">
        <li>
          <svg viewBox="0 0 24 24" aria-hidden="true"><path d="M6.6 10.8a15.1 15.1 0 0 0 6.6 6.6l2.2-2.2a1 1 0 0 1 1-.25 11.4 11.4 0 0 0 3.6.6 1 1 0 0 1 1 1V20a1 1 0 0 1-1 1A17 17 0 0 1 3 4a1 1 0 0 1 1-1h3.5a1 1 0 0 1 1 1 11.4 11.4 0 0 0 .6 3.6 1 1 0 0 1-.25 1z"/></svg>
          0491557203
        </li>
        <li>
          <svg viewBox="0 0 24 24" aria-hidden="true"><path d="M2 5h20v14H2z"/><path d="M2 5l10 8 10-8" fill="none" stroke="#f6f6f6" stroke-width="2"/></svg>
          owen@kvsdonesimply.com.au
        </li>
        <li>
          <svg viewBox="0 0 24 24" aria-hidden="true"><circle cx="12" cy="12" r="11"/><path d="M1 12h22M12 1c4 4 4 18 0 22M12 1c-4 4-4 18 0 22" fill="none" stroke="#f6f6f6" stroke-width="1.5"/></svg>
          www.kvsdonesimply.com.au
        </li>
      </ul>
    </div>
    <div class="footer-band">
      <span class="band-blue"></span>
      <span class="band-orange"></span>
      <span class="band-blue"></span>
      <span class="band-orange"></span>
    </div>
  </section>
</div>
</body>
</html>
```